Automotive eCommerce Business looking for a business card design

Looking for a clean and simple business card design. Our company name is "Brindle Auto" and we are a company specializing in the ecommerce sales of automotive parts, specifically for pick up trucks and large SUVs. Our company colours are red, black, and white.

Feel free to use the logo provided or create a new logo that you seem fit. Looking forward to your creative ideas!

Industry/Entity Type

Automotive

Contact Information for Business Card

We were thinking of a possibly two-sided design featuring just the logo and company name on one side, and personal information on the other side. Single sided designs will be considered as well.

Font styles to use
Serif
Sans Serif
Decorative

Colors
ec1f27
ffffff
000000

Requirements
Must have
• Space for employee's name, title, phone number and email address, along with the company address and website somewhere.

```html
<!DOCTYPE html>
<html lang="en">
<head>
<meta charset="utf-8">
<title>Brindle Auto Ltd. — Business Card</title>
<link rel="stylesheet" href="https://fonts.googleapis.com/css2?family=Cinzel:wght@500&family=Roboto:wght@400;500&family=Roboto+Condensed:wght@500&display=swap">
<style>
  :root {
    --brand-red: #9b1c20;
    --card-white: #f3f3f3;
    --ink: #4a4a4a;
    --backdrop: #2b2b2b;
    --on-red: #ffffff;
  }
  html, body {
    margin: 0;
    width: 1200px;
    height: 960px;
    overflow: hidden;
    background: var(--backdrop);
  }
  .stage { position: relative; width: 1200px; height: 960px; }

  .card {
    position: absolute;
    width: 600px;
    height: 343px;
    box-sizing: border-box;
    box-shadow: 0 3px 8px rgba(0,0,0,.5);
    overflow: hidden;
  }

  /* Front side */
  .card--front { left: 314px; top: 113px; background: var(--card-white); }
  .card--front .accent-band {
    position: absolute; left: 0; right: 0; bottom: 0; height: 15px;
    background: var(--brand-red);
  }
  .person { position: absolute; left: 44px; top: 42px; }
  .person__name {
    margin: 0;
    font: 500 21px/1 "Roboto Condensed", sans-serif;
    color: var(--brand-red);
    letter-spacing: .2px;
  }
  .person__title {
    margin: 6px 0 0;
    font: 500 14px/1 "Roboto", sans-serif;
    color: var(--ink);
  }
  .address {
    position: absolute; left: 44px; top: 155px;
    margin: 0; font: 400 14.5px/19px "Roboto", sans-serif; color: var(--ink);
    font-style: normal;
  }
  .contacts {
    position: absolute; left: 44px; top: 201px;
    margin: 0; padding: 0; list-style: none;
    font: 400 14.5px/19px "Roboto", sans-serif; color: var(--ink);
  }
  .contacts li { display: flex; align-items: center; height: 19px; }
  .contacts svg { width: 13px; height: 13px; margin-right: 10px; fill: var(--brand-red); flex: none; }

  .brand {
    position: absolute; display: flex; flex-direction: column; align-items: center;
  }
  .brand__mark { width: 110px; height: 110px; }
  .brand__name {
    margin: 28px 0 0;
    font: 500 21px/1 "Cinzel", serif;
    white-space: nowrap;
  }
  .card--front .brand { left: 346px; top: 134px; width: 220px; }
  .card--front .brand__mark { background: var(--brand-red); }
  .card--front .brand__name { color: var(--ink); }

  /* Back side */
  .card--back { left: 311px; top: 472px; background: var(--brand-red); }
  .card--back .brand { left: 0; right: 0; top: 68px; }
  .card--back .brand__mark { width: 150px; height: 150px; background: var(--on-red); }
  .card--back .brand__name { margin-top: 24px; font-size: 25px; color: var(--on-red); }
  .card--back .site {
    position: absolute; left: 0; right: 0; top: 293px; margin: 0;
    text-align: center; font: 400 14px/1 "Roboto", sans-serif;
    letter-spacing: 4.6px; color: var(--on-red);
  }
</style>
</head>
<body>
<main class="stage">

  <section class="card card--front" aria-label="Business card front">
    <div class="person">
      <h1 class="person__name">MARA ELLISON</h1>
      <p class="person__title">CEO/FOUNDER</p>
    </div>

    <address class="address">2140 Harlow Street<br>Fairbanks, Alaska 99701</address>

    <ul class="contacts">
      <li>
        <svg viewBox="0 0 16 16" aria-hidden="true"><path d="M3.6 1.2 6 3.6 4.8 5.6c.9 2.1 3.5 4.7 5.6 5.6l2-1.2 2.4 2.4-1.6 2.4C7.9 15 1 8.1.8 2.8Z"/></svg>
        907 555 0142
      </li>
      <li>
        <svg viewBox="0 0 16 16" aria-hidden="true"><path d="M4 0h8v16H4Zm1.5 2v10h5V2Zm2 11.2h1v1.3h-1Z" fill-rule="evenodd"/></svg>
        907 555 0187
      </li>
      <li>
        <svg viewBox="0 0 16 16" aria-hidden="true"><path d="M4 1h8v4H4ZM1 6h14v7h-2v2H3v-2H1Zm4 5v2h6v-2Zm7-3.5h1.5V9H12Z" fill-rule="evenodd"/></svg>
        907 555 0163
      </li>
      <li>
        <svg viewBox="0 0 16 16" aria-hidden="true"><path d="M1 3.5h14v1.2L8 9 1 4.7ZM1 6.3l7 4.3 7-4.3V13H1Z"/></svg>
        mara@brindleauto.com
      </li>
      <li>
        <svg viewBox="0 0 16 16" aria-hidden="true"><circle cx="8" cy="8" r="7"/><path d="M4 5c1.5-.5 2.5.5 2 2s1.5 1.5 1.5 3-1 2.5-1 3M10 3c.5 1.5 2 1.5 3 2.5" stroke="#f3f3f3" stroke-width="1.3" fill="none"/></svg>
        www.brindleauto.com
      </li>
    </ul>

    <div class="brand">
      <div class="brand__mark" aria-hidden="true"></div>
      <p class="brand__name">Brindle Auto Ltd.</p>
    </div>

    <div class="accent-band"></div>
  </section>

  <section class="card card--back" aria-label="Business card back">
    <div class="brand">
      <div class="brand__mark" aria-hidden="true"></div>
      <p class="brand__name">Brindle Auto Ltd.</p>
    </div>
    <p class="site">www.brindleauto.com</p>
  </section>

</main>
</body>
</html>
```